Independent Financial Advisor Billboard Campaign - Maple Crest Financial

I am a local, independent financial advisor. My company is Maple Crest Financial, located in Charleston, WV. My main source of revenue comes from those nearing or entering retirement that need assistance with financial planning and investment management. Many are looking to rollover their employer retirement plan into an IRA account. I would like a billboard design campaign that focuses on this type of client. Please see our website www.maplecrestfinancial.com for more information.

```html
<!DOCTYPE html>
<html lang="en">
<head>
<meta charset="utf-8">
<title>Maple Crest Financial – Retirement Done Right Billboard</title>
<link href="https://fonts.googleapis.com/css2?family=League+Spartan:wght@700;800&family=Montserrat:wght@500;600&display=swap" rel="stylesheet">
<style>
  :root {
    --navy: #1a3d6e;
    --band: #17386a;
    --band-deep: #122e58;
    --silver: #a8a8a8;
    --paper: #ffffff;
    --icon-grey: #9a9a9a;
    --url-tint: #e3e8f0;
    --photo-light: #b9b9b9;
    --photo-dark: #6c6c6c;
  }
  html, body {
    margin: 0;
    padding: 0;
    width: 1050px;
    height: 1200px;
    overflow: hidden;
    background: var(--paper);
  }
  .canvas {
    position: relative;
    width: 1050px;
    height: 1200px;
  }
  .billboard {
    position: absolute;
    left: 45px;
    top: 460px;
    width: 960px;
    height: 279px;
    box-shadow: 0 2px 6px rgba(0,0,0,0.25);
  }
  .headline {
    font-family: "League Spartan", "Montserrat", sans-serif;
    font-weight: 800;
  }
  .headline--primary { fill: var(--navy); }
  .headline--secondary { fill: var(--silver); }
  .brand-name {
    font-family: "Montserrat", sans-serif;
    font-weight: 600;
    fill: var(--paper);
    letter-spacing: 1px;
  }
  .phone-number {
    font-family: "League Spartan", "Montserrat", sans-serif;
    font-weight: 700;
    fill: var(--paper);
  }
  .web-address {
    font-family: "Montserrat", sans-serif;
    font-weight: 500;
    fill: var(--url-tint);
  }
</style>
</head>
<body>
<main class="canvas">
  <svg class="billboard" viewBox="0 0 960 279" width="960" height="279" xmlns="http://www.w3.org/2000/svg">
    <defs>
      <linearGradient id="band-fill" x1="0" y1="0" x2="1" y2="1">
        <stop offset="0" stop-color="var(--band-deep)"/>
        <stop offset="0.5" stop-color="var(--band)"/>
        <stop offset="1" stop-color="var(--band-deep)"/>
      </linearGradient>
      <linearGradient id="portrait-fill" x1="0" y1="0" x2="1" y2="1">
        <stop offset="0" stop-color="var(--photo-light)"/>
        <stop offset="1" stop-color="var(--photo-dark)"/>
      </linearGradient>
    </defs>

    <rect class="panel-background" x="0" y="0" width="960" height="279" fill="var(--paper)"/>

    <rect class="contact-band" x="0" y="173" width="724" height="106" fill="url(#band-fill)"/>

    <rect class="advisor-portrait" x="724" y="0" width="236" height="279" fill="url(#portrait-fill)"
          role="img" aria-label="Portrait photo of the advisor in a white polo shirt before a grey brick wall"/>

    <text class="headline headline--primary" x="37" y="90" font-size="88" textLength="566" lengthAdjust="spacingAndGlyphs">RETIREMENT</text>
    <text class="headline headline--secondary" x="37" y="164" font-size="88" textLength="605" lengthAdjust="spacingAndGlyphs">DONE RIGHT!</text>

    <g class="brand">
      <rect class="brand-mark" x="37" y="196" width="40" height="40" fill="var(--paper)"/>
      <text class="brand-name" x="92" y="214" font-size="17" textLength="200" lengthAdjust="spacingAndGlyphs">MAPLE CREST</text>
      <text class="brand-name" x="92" y="236" font-size="13" letter-spacing="5">FINANCIAL</text>
    </g>

    <g class="phone-icon">
      <circle cx="372" cy="207" r="16" fill="var(--icon-grey)"/>
      <path d="M365.5 199.5c1-1 2-1 2.6 0l1.8 2.6c.5.8.3 1.6-.4 2.1l-1 .8c.8 2 2.4 3.6 4.4 4.6l.8-1c.6-.7 1.4-.8 2.1-.3l2.6 1.8c.9.6.9 1.6 0 2.6l-1.1 1.2c-1 1-2.4 1.2-3.8.6-4.6-2-8.2-5.6-10.1-10.2-.6-1.4-.3-2.8.7-3.8z" fill="var(--paper)"/>
      <path d="M374 198.5a6.5 6.5 0 0 1 6 6" stroke="var(--paper)" stroke-width="1.4" fill="none" stroke-linecap="round"/>
      <path d="M374 201.8a3.4 3.4 0 0 1 2.8 2.8" stroke="var(--paper)" stroke-width="1.4" fill="none" stroke-linecap="round"/>
    </g>

    <text class="phone-number" x="401" y="222" font-size="44" textLength="291" lengthAdjust="spacingAndGlyphs">304.555.0142</text>
    <text class="web-address" x="356" y="251" font-size="17" textLength="335" lengthAdjust="spacingAndGlyphs">www.maplecrestfinancial.com</text>
  </svg>
</main>
</body>
</html>
```